Redesign of business card for Cedar Ridge Mechanical

We are looking for a new design for our business cards for Cedar Ridge Mechanical. We are a plumbing & HVAC construction company, operating on the West Coast of Canada and USA. Logo attached.
Industry/Entity Type
Construction - Plumbing & HVAC
Contact Information for Business Card
Name, address, phone numbers, email, website address
Look and feel
Each slider illustrates characteristics of the customer's brand and the style your logo design should communicate.

```html
<!DOCTYPE html>
<html lang="en">
<head>
<meta charset="UTF-8">
<title>Cedar Ridge Mechanical — Business Card</title>
<link rel="stylesheet" href="https://fonts.googleapis.com/css2?family=Montserrat:wght@400;500;700&display=swap">
<style>
  :root {
    --backdrop: #e9e6e1;
    --card-dark: #232323;
    --card-dark-sheen: #3a3a3a;
    --card-light: #ffffff;
    --ink: #1c1c1c;
    --ink-inverse: #ffffff;
    --band: #1c1c1c;
  }
  * { margin: 0; padding: 0; box-sizing: border-box; }
  html, body { width: 1200px; height: 900px; overflow: hidden; }
  body {
    background: var(--backdrop);
    font-family: "Montserrat", sans-serif;
    color: var(--ink);
    position: relative;
  }
  .card {
    position: absolute;
    width: 600px;
    height: 343px;
    border-radius: 22px;
    overflow: hidden;
    box-shadow: 0 10px 24px rgba(0,0,0,0.18);
  }

  /* Front */
  .card-front {
    left: 360px; top: 60px;
    background: linear-gradient(135deg, var(--card-dark) 0%, var(--card-dark-sheen) 55%, var(--card-dark) 100%);
    display: flex; align-items: center; justify-content: center;
  }
  .front-wordmark {
    display: flex; align-items: center; gap: 16px;
    color: var(--ink-inverse);
  }
  .wordmark-square {
    width: 26px; height: 26px;
    background: var(--ink-inverse);
    flex: none;
  }
  .wordmark-name {
    font-weight: 700;
    font-size: 30px;
    letter-spacing: 1px;
    text-transform: uppercase;
    white-space: nowrap;
  }

  /* Back */
  .card-back {
    left: 200px; top: 480px;
    background: var(--card-light);
  }
  .back-band {
    position: absolute; left: 0; right: 0; bottom: 0;
    height: 18px; background: var(--band);
  }
  .back-wordmark {
    position: absolute; right: 44px; top: 70px;
    display: flex; align-items: center; gap: 10px;
    color: var(--ink);
  }
  .back-wordmark .wordmark-square { width: 18px; height: 18px; background: var(--ink); }
  .back-wordmark .wordmark-name { font-size: 19px; }

  .person {
    position: absolute; left: 40px; top: 104px;
  }
  .person-name { font-weight: 700; font-size: 24px; line-height: 1.1; }
  .person-title { font-weight: 400; font-size: 14px; margin-top: 2px; }

  .divider {
    position: absolute; left: 40px; right: 44px; top: 160px;
    height: 2px; background: var(--ink);
  }

  .contact-list {
    position: absolute; left: 40px; top: 176px;
    list-style: none;
    font-size: 14px;
  }
  .contact-list li { display: flex; align-items: center; gap: 10px; height: 24px; white-space: nowrap; }
  .contact-list svg { width: 14px; height: 14px; flex: none; }

  .address {
    position: absolute; right: 44px; top: 256px;
    font-size: 15px; line-height: 1.3; text-align: left;
  }
</style>
</head>
<body>

  <section class="card card-front" aria-label="Card front">
    <div class="front-wordmark">
      <span class="wordmark-square"></span>
      <span class="wordmark-name">Cedar Ridge Mechanical</span>
    </div>
  </section>

  <section class="card card-back" aria-label="Card back">
    <div class="back-wordmark">
      <span class="wordmark-square"></span>
      <span class="wordmark-name">Cedar Ridge Mechanical</span>
    </div>

    <div class="person">
      <p class="person-name">Daniel Brooks</p>
      <p class="person-title">Managing Director</p>
    </div>

    <div class="divider"></div>

    <ul class="contact-list">
      <li>
        <svg viewBox="0 0 24 24" aria-hidden="true"><path fill="#1c1c1c" d="M6.6 10.8a15.1 15.1 0 0 0 6.6 6.6l2.2-2.2a1 1 0 0 1 1-.25 11.4 11.4 0 0 0 3.6.57 1 1 0 0 1 1 1V20a1 1 0 0 1-1 1A17 17 0 0 1 3 4a1 1 0 0 1 1-1h3.5a1 1 0 0 1 1 1c0 1.25.2 2.45.57 3.57a1 1 0 0 1-.25 1z"/></svg>
        888.555.0142
      </li>
      <li>
        <svg viewBox="0 0 24 24" aria-hidden="true"><rect x="2" y="5" width="20" height="14" fill="#1c1c1c"/><path d="M3 6l9 7 9-7" stroke="#fff" stroke-width="1.6" fill="none"/></svg>
        info@cedarridgemechanical.com
      </li>
      <li>
        <svg viewBox="0 0 24 24" aria-hidden="true"><circle cx="12" cy="12" r="10" fill="#1c1c1c"/><path d="M2 12h20M12 2c3 3 3 17 0 20M12 2c-3 3-3 17 0 20" stroke="#fff" stroke-width="1.5" fill="none"/></svg>
        www.cedarridgemechanical.com
      </li>
    </ul>

    <p class="address">482 Timber Lane<br>Jackson, MS 39201</p>

    <div class="back-band"></div>
  </section>

</body>
</html>
```